Online training business needs new website

We need a new wordpress website as a result of a rebranding. The business is a crisis management training company focussed on online training and simulation exercises. We only need a 4 page site - home, about us, contact us and blog. However we must be able to add additional tabs in the header to redirect to our sales and marketing system (Kartra). As these change from time to time, we must be able to add and delete as required.The site must be editable by us, with a basic understanding of wordpress and no understanding of coding. We don't want to have to employ someone to change text, add posts or add a new workshops etc. The theme chosen must be easy to edit by a beginner.

Target Market(s)

Senior managers food and consumer goods companies

Industry/Entity Type

Consulting

Coding

Coded - Design and coding required

Font styles to use
Sans Serif

Requirements
Must have
• Home page, about us, contact us, blog
• Colour scheme from logo (attached) - maroon, blue and grey
• If you go to the current website "tidewellcollege.com" and click on the "workshops" tab you will see the content I need on the home page for the plumvantage.com site
Nice to have
• Modern, simple and minimalist design is preferred

```html
<!DOCTYPE html>
<html lang="en">
<head>
<meta charset="utf-8">
<title>Plum Vantage – Online Crisis Management Training</title>
<link href="https://fonts.googleapis.com/css2?family=Roboto:wght@300;400;500;700&family=Open+Sans:wght@400;600&display=swap" rel="stylesheet">
<style>
:root{
  --maroon:#7d0a3d;
  --navy:#0e3a6b;
  --blue:#0f4a80;
  --sky:#dde9f6;
  --sky-light:#f3f7fc;
  --grey-line:#c9d5e2;
  --text:#444;
  --white:#fff;
}
*{box-sizing:border-box;margin:0;padding:0}
html,body{width:1200px;height:2826px;overflow:hidden}
body{position:relative;background:var(--white);font-family:'Roboto',Arial,sans-serif;color:var(--navy)}
.abs{position:absolute}
.hero-bg{left:0;top:0;width:1200px;height:760px;background:linear-gradient(180deg,var(--sky-light) 0%,var(--sky) 100%)}
.brand{left:172px;top:36px;display:flex;align-items:center;gap:12px}
.brand-dot{width:46px;height:46px;border-radius:50%;background:var(--maroon)}
.brand-name{font-weight:700;font-size:34px;color:var(--maroon);letter-spacing:.5px}
.main-nav{top:52px;left:546px;display:flex;gap:0}
.main-nav a{position:absolute;font-size:19px;color:var(--navy);text-decoration:none;white-space:nowrap}
.main-nav a.active{color:var(--maroon)}
.hero-kicker{left:168px;top:256px;font-size:31px;font-weight:300;color:var(--navy)}
.hero-line{left:166px;top:298px;font-size:36px;font-weight:700;color:var(--maroon)}
.hero-title{left:164px;top:340px;font-size:42px;font-weight:700;color:var(--navy)}
.btn{display:inline-flex;align-items:center;justify-content:center;border-radius:30px;background:var(--maroon);color:var(--white);font-size:19px;text-decoration:none}
.hero-btn{left:168px;top:410px;width:184px;height:58px}
.hero-art{left:620px;top:150px;width:440px;height:420px;border-radius:50%;background:radial-gradient(circle at 50% 50%,#f2c53a 0%,#e8b830 30%,#c8d6e4 60%,rgba(200,214,228,0) 72%)}
.divider{left:0;top:640px}
.about-title{left:0;width:1200px;top:746px;text-align:center;font-size:36px;font-weight:400;color:var(--navy)}
.about-title span{color:var(--maroon)}
.about-text{left:230px;width:740px;top:806px;text-align:center;font-family:'Open Sans',Arial,sans-serif;font-size:18.5px;line-height:31px;color:var(--text)}
.fact{width:428px;height:168px;background:var(--white);box-shadow:0 0 6px rgba(0,0,0,.18);display:flex;align-items:center;padding:0 24px 0 26px;gap:22px;font-size:18.5px;line-height:27px;color:var(--navy)}
.fact.featured{background:linear-gradient(135deg,#16336e 0%,#4b1d5e 55%,var(--maroon) 100%);color:var(--white)}
.fact-icon{flex:0 0 84px;height:84px;position:relative}
.blogs-band{left:0;top:1380px}
.blogs-mark{left:588px;top:1438px;width:24px;height:24px;border-radius:50%;border:3px solid var(--white)}
.blogs-title{left:0;width:1200px;top:1476px;text-align:center;font-size:36px;color:var(--white)}
.post{background:var(--white);overflow:hidden}
.post-img{background:linear-gradient(135deg,#5b5148,#2b2622)}
.post-date{font-size:12.5px;font-weight:700;color:var(--maroon);display:flex;align-items:center;gap:6px}
.post-title{font-size:19px;color:var(--blue);margin-top:10px}
.post-excerpt{font-family:'Open Sans',Arial,sans-serif;font-size:12.5px;line-height:18px;color:#777;margin-top:8px}
.post-more{display:block;font-size:12.5px;color:var(--blue);margin-top:14px;text-decoration:none}
.post-lg{left:148px;top:1560px;width:434px;height:385px}
.post-lg .post-img{height:210px}
.post-lg .post-body{padding:18px 24px}
.post-sm{width:445px;height:186px;display:flex}
.post-sm .post-img{flex:0 0 215px;height:100%}
.post-sm .post-body{padding:20px 16px 0 24px}
.contact-form{left:170px;top:2170px;width:444px;height:393px;background:var(--maroon);padding:30px 40px 0 40px}
.field{display:block;border-bottom:1px solid rgba(255,255,255,.7);font-size:15px;color:var(--white);padding-bottom:8px;margin-bottom:34px}
.field.message{height:96px}
.submit{display:inline-flex;align-items:center;justify-content:center;width:176px;height:46px;background:var(--navy);color:var(--white);font-size:19px;font-weight:500;margin-top:-10px}
.contact-info{left:682px;top:2170px;width:380px}
.contact-info h2{font-size:32px;font-weight:400;color:var(--navy);margin-bottom:22px}
.info-label{font-size:15px;font-weight:500;color:#333;margin-top:24px}
.info-label:first-of-type{margin-top:0}
.info-value{font-size:17px;line-height:26px;color:#333;margin-top:4px}
.social{display:flex;gap:30px;margin-top:16px}
.social span{width:22px;height:22px;border-radius:50%;background:var(--maroon)}
.site-footer{left:0;top:2675px;width:1200px;height:151px;background:var(--white)}
.footer-nav a{position:absolute;top:46px;font-size:19px;color:var(--navy);text-decoration:none}
.copyright{position:absolute;left:0;width:1200px;top:92px;text-align:center;font-size:16px;color:#444}
.contact-bg{left:0;top:2080px;width:1200px;height:595px;background:var(--sky-light)}
</style>
</head>
<body>

<div class="abs hero-bg"></div>

<header>
  <div class="abs brand"><span class="brand-dot"></span><span class="brand-name">PLUM VANTAGE</span></div>
  <nav class="abs main-nav" aria-label="Main">
    <a class="active" style="left:30px">HOME</a>
    <a style="left:124px">ABOUT US</a>
    <a style="left:252px">CONTACT US</a>
    <a style="left:404px">BLOG</a>
  </nav>
</header>

<section class="hero">
  <p class="abs hero-kicker">WE PROVIDE</p>
  <p class="abs hero-line">ONLINE TRAINING FOR</p>
  <h1 class="abs hero-title">CRISIS MANAGEMENT</h1>
  <a class="abs btn hero-btn">READ MORE</a>
  <div class="abs hero-art" role="img" aria-label="Illustration of an hourglass with a person sinking in the sand"></div>
</section>

<svg class="abs divider" width="1200" height="130" viewBox="0 0 1200 130">
  <path d="M0 130 Q600 -10 1200 130 L1200 130 Z" fill="#fff"/>
  <path d="M130 76 Q370 44 560 40" stroke="var(--navy)" stroke-width="5" fill="none"/>
  <path d="M640 40 Q830 44 1070 76" stroke="var(--navy)" stroke-width="5" fill="none"/>
  <circle cx="600" cy="35" r="34" fill="#fff"/>
  <circle cx="600" cy="35" r="22" fill="none" stroke="var(--maroon)" stroke-width="5"/>
</svg>

<section class="about">
  <h2 class="abs about-title">ABOUT <span style="color:var(--navy)">PLUM VANTAGE</span></h2>
  <p class="abs about-text">If you are a food or consumer goods manufacturer, distributor or retailer, a major incident or a product recall can quickly escalate into a crisis!</p>

  <div class="abs fact featured" style="left:160px;top:935px">
    <svg class="fact-icon" viewBox="0 0 84 84"><circle cx="42" cy="42" r="34" fill="none" stroke="rgba(255,255,255,.35)" stroke-width="5"/><circle cx="42" cy="42" r="16" fill="none" stroke="#fff" stroke-width="2.5"/><text x="42" y="49" text-anchor="middle" font-size="20" fill="#fff" font-family="Roboto,sans-serif">$</text></svg>
    <p>The average cost of a crisis is $10m and 25% cost over $100m</p>
  </div>
  <div class="abs fact" style="left:606px;top:935px">
    <svg class="fact-icon" viewBox="0 0 84 84"><circle cx="42" cy="42" r="34" fill="none" stroke="var(--grey-line)" stroke-width="5"/><polyline points="22,32 36,46 46,38 62,54" fill="none" stroke="var(--maroon)" stroke-width="2.5"/><circle cx="22" cy="32" r="3.5" fill="var(--maroon)"/><circle cx="36" cy="46" r="3.5" fill="var(--maroon)"/><circle cx="46" cy="38" r="3.5" fill="var(--maroon)"/><path d="M58 54 L64 55 L62 49" fill="none" stroke="var(--maroon)" stroke-width="2.5"/></svg>
    <p>Small and medium size businesses often don't survive at all</p>
  </div>
  <div class="abs fact" style="left:160px;top:1122px">
    <svg class="fact-icon" viewBox="0 0 84 84"><circle cx="42" cy="42" r="34" fill="none" stroke="var(--grey-line)" stroke-width="5"/><rect x="30" y="30" width="24" height="24" rx="4" fill="none" stroke="var(--maroon)" stroke-width="2.5"/><path d="M37 37 L47 47 M47 37 L37 47" stroke="var(--maroon)" stroke-width="2.5"/></svg>
    <p>The largest cost to any size business is to your reputation &amp; brand - that impacts customer relationships &amp; long term sales!</p>
  </div>
  <div class="abs fact" style="left:606px;top:1122px">
    <svg class="fact-icon" viewBox="0 0 84 84"><circle cx="42" cy="42" r="34" fill="none" stroke="var(--grey-line)" stroke-width="5"/><path d="M42 22 L64 58 L20 58 Z" fill="none" stroke="var(--maroon)" stroke-width="3" stroke-linejoin="round"/><path d="M42 35 L42 48" stroke="var(--maroon)" stroke-width="3"/><circle cx="42" cy="53" r="2" fill="var(--maroon)"/></svg>
    <p>Reputation risk remains the number one concern of senior executives, but most are unprepared for a crisis</p>
  </div>
</section>

<div class="abs contact-bg"></div>

<svg class="abs blogs-band" width="1200" height="710" viewBox="0 0 1200 710">
  <defs>
    <linearGradient id="bandFill" x1="0" y1="0" x2="1" y2="1">
      <stop offset="0" stop-color="#0d4c86"/><stop offset="1" stop-color="#0a3a6a"/>
    </linearGradient>
  </defs>
  <path d="M0 50 Q600 -30 1200 40 L1200 640 Q700 760 0 600 Z" fill="var(--maroon)"/>
  <path d="M0 70 Q600 -5 1200 48 L1200 626 Q700 738 0 590 Z" fill="url(#bandFill)"/>
</svg>

<section class="blogs">
  <span class="abs blogs-mark"></span>
  <h2 class="abs blogs-title">OUR BLOGS</h2>

  <article class="abs post post-lg">
    <div class="post-img" role="img" aria-label="Photo of a hand stopping a row of falling dominoes"></div>
    <div class="post-body">
      <p class="post-date"><svg width="13" height="13" viewBox="0 0 13 13"><rect x="1" y="2" width="11" height="10" fill="none" stroke="var(--maroon)" stroke-width="1.6"/><path d="M1 5 H12" stroke="var(--maroon)" stroke-width="1.6"/></svg>30 DEC 2018</p>
      <h3 class="post-title" style="font-weight:400">Pellentesque faucibus Ut accumsan ultricies</h3>
      <p class="post-excerpt">Pellentesque faucibus Ut accumsan ultricies elit Maecenas at justo id velit placerat molestie Donec dictum lectus non</p>
      <a class="post-more">READ MORE</a>
    </div>
  </article>

  <article class="abs post post-sm" style="left:598px;top:1560px">
    <div class="post-img" role="img" aria-label="Photo of a team reviewing charts and a tablet at a desk" style="background:linear-gradient(135deg,#8a9a8c,#4c5a63)"></div>
    <div class="post-body">
      <p class="post-date"><svg width="13" height="13" viewBox="0 0 13 13"><rect x="1" y="2" width="11" height="10" fill="none" stroke="var(--maroon)" stroke-width="1.6"/><path d="M1 5 H12" stroke="var(--maroon)" stroke-width="1.6"/></svg>21 DEC 2018</p>
      <h3 class="post-title" style="font-weight:400">Blog Title here</h3>
      <p class="post-excerpt">Pellentesque faucibus Ut accumsan ultricies elit Maecenas at justo id velit placerat</p>
      <a class="post-more">READ MORE</a>
    </div>
  </article>

  <article class="abs post post-sm" style="left:598px;top:1760px">
    <div class="post-img" role="img" aria-label="Photo of a business meeting around a table" style="background:linear-gradient(135deg,#b9b2a6,#5a5048)"></div>
    <div class="post-body">
      <p class="post-date"><svg width="13" height="13" viewBox="0 0 13 13"><rect x="1" y="2" width="11" height="10" fill="none" stroke="var(--maroon)" stroke-width="1.6"/><path d="M1 5 H12" stroke="var(--maroon)" stroke-width="1.6"/></svg>14 DEC 2018</p>
      <h3 class="post-title" style="font-weight:400">Blog Title here</h3>
      <p class="post-excerpt">Pellentesque faucibus Ut accumsan ultricies elit Maecenas at justo id velit placerat</p>
      <a class="post-more">READ MORE</a>
    </div>
  </article>
</section>

<section class="contact">
  <form class="abs contact-form">
    <span class="field">NAME</span>
    <span class="field">EMAIL</span>
    <span class="field">PHONE NUMBER</span>
    <span class="field message">MESSAGE</span>
    <span class="submit">SUBMIT</span>
  </form>
  <div class="abs contact-info">
    <h2>CONTACT US</h2>
    <p class="info-label">ADDRESS</p>
    <p class="info-value">14 HARBOURNE LANE, WESTFIELD WA 6021<br>PERTH – AUSTRALIA</p>
    <p class="info-label">PHONE NUMBER</p>
    <p class="info-value">0400 555 218</p>
    <p class="info-label">EMAIL US</p>
    <p class="info-value">INFO@PLUMVANTAGE.COM</p>
    <p class="info-label">FOLLOW US</p>
    <div class="social" aria-label="Social links"><span></span><span></span><span></span><span></span></div>
  </div>
</section>

<footer class="abs site-footer">
  <nav class="footer-nav" aria-label="Footer">
    <a style="left:368px">HOME</a>
    <a style="left:470px">ABOUT US</a>
    <a style="left:608px">CONTACT US</a>
    <a style="left:772px">BLOG</a>
  </nav>
  <p class="copyright">© 2019 Company Name &nbsp;All right reserved</p>
</footer>

</body>
</html>
```